The design should look similar to the uploaded example to accommodate the information needed for a business card template. I would like to see the colors orange and charcoal grey incorporated along with the logo.The following should be on the back of the card SPECIALIZING IN NEW AND USED TIRES & WHEELS FOR:- Loaders- Skid Steers- Telehandlers- Boom Lifts- Forklifs and moreELIMINATING DOWNTIMEWheel Exchange Program for New & Used Foam Filled and Solid Rubber TiresSPECIALTY SERVICES- Foam Filling Tires- Largest Tire Press in SE- ONSITE Forklift Tire Press- Boom Truck Services - Rubber Tracks

Target Market(s)

New and Existing Customers

Industry/Entity Type

Business

Contact Information for Business Card

NAMEHEAVY DUTY TIRE, LLC8470 Belvedere RoadWest Palm Beach, FL 33411P: 844-HD-TIRESF: 561-431-6469C:E: W: WWW.GRANITERIMSUPPLY-EXAMPLE.COM

Font styles to use
Sans Serif

Colors
f37122
333333

Requirements
Must have
• The logo and the information indicated for the backside of the card
Nice to have
• Keep the orange and charcoal grey colors

```html
<!DOCTYPE html>
<html lang="en">
<head>
<meta charset="utf-8">
<title>Granite Rim Supply – Business Card</title>
<link rel="stylesheet" href="https://fonts.googleapis.com/css2?family=Open+Sans:wght@400;600;700&display=swap">
<style>
  :root{
    --orange:#f58a3c;
    --orange-deep:#f37122;
    --charcoal:#333d3a;
    --ink:#222222;
    --paper:#ffffff;
    --backdrop:#ece9e6;
  }
  *{margin:0;padding:0;box-sizing:border-box}
  html,body{width:1200px;height:900px;overflow:hidden}
  body{background:var(--backdrop);font-family:"Open Sans",Arial,sans-serif;position:relative}
  .card{position:absolute;background:var(--paper);overflow:hidden;box-shadow:0 4px 14px rgba(0,0,0,.18)}
  .card svg.bands{position:absolute;left:0;top:0}
  .card-front{left:78px;top:35px;width:588px;height:363px}
  .card-back{left:388px;top:505px;width:567px;height:352px}
  .brand-mark{position:absolute;border-radius:50%;background:var(--charcoal)}
  .card-front .brand-mark{left:62px;top:26px;width:110px;height:110px}
  .card-back .brand-mark{left:54px;top:18px;width:112px;height:112px}
  .company{position:absolute;left:229px;top:58px;font-weight:700;line-height:1.1}
  .company-name{color:var(--orange);font-size:31px;display:block}
  .company-suffix{color:var(--charcoal);font-size:31px;display:block}
  .contact-list{position:absolute;right:306px;top:210px;list-style:none;color:var(--paper);font-size:15px;text-align:right}
  .contact-list li{height:24.5px;display:flex;justify-content:flex-end;align-items:center;gap:9px;white-space:nowrap}
  .contact-list svg{width:12px;height:12px;fill:var(--paper)}
  .person{position:absolute;left:315px;top:233px;color:var(--paper)}
  .person-name{font-size:21px;font-weight:600;margin-bottom:6px}
  .person-address{font-size:15px;line-height:24px}
  .tagline{position:absolute;left:197px;top:42px}
  .tagline-head{color:var(--orange);font-size:16px;font-weight:700;margin-bottom:4px}
  .tagline-body{color:var(--ink);font-size:17px;font-weight:600;line-height:22px}
  .services{position:absolute;right:322px;top:182px;color:var(--paper);text-align:right}
  .services h2{font-size:19px;font-weight:700;margin-bottom:12px}
  .services li{list-style:none;font-size:15px;font-weight:600;height:23.5px}
  .services li::after{content:"";display:inline-block;width:6px;height:6px;border-radius:50%;background:var(--paper);margin-left:9px;vertical-align:middle}
  .equipment{position:absolute;left:300px;top:182px;color:var(--paper)}
  .equipment h2{font-size:17px;font-weight:700;line-height:23px;margin-bottom:12px}
  .equipment li{list-style:none;font-size:15px;font-weight:600;height:23.5px}
  .equipment li::before{content:"";display:inline-block;width:6px;height:6px;border-radius:50%;background:var(--paper);margin-right:6px;vertical-align:middle}
</style>
</head>
<body>

<section class="card card-front">
  <svg class="bands" width="588" height="363" viewBox="0 0 588 363">
    <polygon fill="#333d3a" points="0,171 402,171 387,196 0,196"/>
    <polygon fill="#f58a3c" points="0,200 392,200 413,163 588,163 588,363 0,363"/>
  </svg>
  <div class="brand-mark"></div>
  <h1 class="company">
    <span class="company-name">GRANITE RIM SUPPLY</span>
    <span class="company-suffix">LLC</span>
  </h1>
  <ul class="contact-list">
    <li>844-GR-WHEEL <svg viewBox="0 0 12 12"><path d="M2 1l2 0 1 3-1.5 1c.7 1.4 1.8 2.5 3.2 3.2L7.7 6.7l3 1v2.3c0 .6-.5 1-1 1C4.8 11 1 7.2 1 2c0-.5.4-1 1-1z"/></svg></li>
    <li>561-278-9053 <svg viewBox="0 0 12 12"><path d="M3 1h5v3H3zM1 4h10v6H9V8H3v2H1zM3 9h6v2H3z"/></svg></li>
    <li>123-456-7890 <svg viewBox="0 0 12 12"><path d="M3 0h6a1 1 0 0 1 1 1v10a1 1 0 0 1-1 1H3a1 1 0 0 1-1-1V1a1 1 0 0 1 1-1zm0 2v7h6V2z"/></svg></li>
    <li>info@graniterim-example.com <svg viewBox="0 0 12 12"><path d="M0 2h12v8H0zm1 1v.4l5 3.3 5-3.3V3zm0 1.6V9h10V4.6L6 7.9z"/></svg></li>
    <li>www.graniterimsupply-example.com <svg viewBox="0 0 12 12"><circle cx="6" cy="6" r="5.5"/></svg></li>
  </ul>
  <div class="person">
    <p class="person-name">Daniel Okafor</p>
    <p class="person-address">5126 Marston Lane<br>West Palm Beach, FL 33411</p>
  </div>
</section>

<section class="card card-back">
  <svg class="bands" width="567" height="352" viewBox="0 0 567 352">
    <polygon fill="#333d3a" points="0,145 398,145 383,170 0,170"/>
    <polygon fill="#f58a3c" points="0,174 387,174 410,138 567,138 567,352 0,352"/>
  </svg>
  <div class="brand-mark"></div>
  <div class="tagline">
    <p class="tagline-head">ELIMINATING DOWNTIME</p>
    <p class="tagline-body">Wheel Exchange Program for New &amp;<br>Used Foam Filled and Solid Rubber Tires</p>
  </div>
  <div class="services">
    <h2>SPECIALTY SERVICES</h2>
    <ul>
      <li>Foam Filling Tires</li>
      <li>Largest Tire Press in SE</li>
      <li>ONSITE Forklift Tire Press</li>
      <li>Boom Truck Services</li>
      <li>Rubber Tracks</li>
    </ul>
  </div>
  <div class="equipment">
    <h2>SPECIALIZING IN NEW AND<br>USED TIRES &amp; WHEELS FOR:</h2>
    <ul>
      <li>Loaders</li>
      <li>Skid Steers</li>
      <li>TelehandlersBoom Lifts</li>
      <li>Forklifs and more</li>
    </ul>
  </div>
</section>

</body>
</html>
```